Kelvaro.ch is looking for business card letterhead and envelope C5 with WOW effect

We need a strong business card for our company Kelvaro.ch, logo is available. You want a black or dark background on which the logo Stark r% 26 # 252; appears. Letterhead and envelope in C5 format should be in a similar design, but does not have to be We need a strong business card for our company Kelvaro.ch, logo is available. A black or dark background is desired, on which the logo Stark comes across. The letterhead and the envelope in C5 format should have a similar design.

Target Market(s)

Private customers as well as entrepreneurs

Contact Information for Business Card

E-mail: info@kelvaro-example.ch
Web.www.Kelvaro-example.ch
Tel: +41 ( 0 ) 79 482 6037
Adresse:
Lindenweg 14
9406 Tarnbach

Hier kann man Icons verwenden für Email,Tel und Adressse

Font styles to use
Other font styles liked:
• Dubai,bold

Colors

Designer to choose colors to be used in the design.

Requirements
Must have
• WOW effect
Nice to have
• R% 26 # 252; back business card with our service listings. - VEHICLE LABELING - SHOP WINDOW LABELING - STICKERS AND MUCH MORE ... in red color

```html
<!DOCTYPE html>
<html lang="en">
<head>
<meta charset="utf-8">
<title>Kelvaro.ch business card</title>
<link href="https://fonts.googleapis.com/css2?family=Roboto:wght@300;400;500;700&display=swap" rel="stylesheet">
<style>
  :root {
    --bg: #dcdcdc;
    --card: #303033;
    --accent: #f5c518;
    --text: #f2f2f2;
    --muted: #5a5a5e;
    --rule: #8a8a8a;
  }
  * { box-sizing: border-box; margin: 0; padding: 0; }
  html, body { width: 1200px; height: 880px; overflow: hidden; }
  body {
    background: var(--bg);
    font-family: 'Roboto', sans-serif;
    position: relative;
  }
  .card {
    position: absolute;
    width: 560px;
    height: 320px;
    background: var(--card);
    border-bottom: 4px solid var(--accent);
    box-shadow: 0 10px 30px rgba(0,0,0,.25);
  }
  .card--services { left: 80px; top: 100px; }
  .card--contact { left: 560px; top: 460px; }

  /* services side */
  .brand-faint {
    position: absolute; left: 120px; top: 62px;
    display: flex; align-items: center; gap: 14px;
  }
  .brand-faint .mark { width: 46px; height: 46px; border-radius: 50%; background: var(--muted); }
  .brand-faint .name {
    font-weight: 700; font-size: 44px; color: var(--muted);
    letter-spacing: 1px; text-transform: uppercase;
  }
  .services {
    position: absolute; left: 0; right: 0; top: 176px; text-align: center;
  }
  .services__title {
    color: var(--accent); font-weight: 500; font-size: 28px; margin-bottom: 18px;
  }
  .services__list {
    color: var(--text); font-weight: 300; font-size: 17px; line-height: 1.45;
    text-transform: uppercase; letter-spacing: .3px;
  }
  .services__list .dot {
    display: inline-block; width: 9px; height: 9px; border-radius: 50%;
    background: var(--accent); margin: 0 6px; vertical-align: middle;
  }

  /* contact side */
  .brand {
    position: absolute; left: 44px; top: 132px;
    display: flex; align-items: center; gap: 12px;
  }
  .brand .mark { width: 34px; height: 34px; border-radius: 50%; background: var(--accent); }
  .brand .name {
    font-weight: 700; font-size: 28px; color: var(--text);
    text-transform: uppercase; letter-spacing: .5px;
  }
  .divider {
    position: absolute; left: 290px; top: 60px; width: 1px; height: 190px;
    background: var(--rule);
  }
  .details { position: absolute; left: 316px; top: 62px; color: var(--text); }
  .person__name { color: var(--accent); font-weight: 700; font-size: 24px; }
  .person__role { font-weight: 300; font-size: 15px; margin: 2px 0 16px 6px; }
  .row {
    display: flex; align-items: flex-start; gap: 10px;
    font-weight: 300; font-size: 15px; line-height: 1.3; margin-bottom: 6px;
  }
  .row svg { width: 14px; height: 14px; flex: none; margin-top: 2px; fill: var(--accent); }
  .address { margin-bottom: 14px; }
</style>
</head>
<body>

<section class="card card--services">
  <div class="brand-faint">
    <span class="mark"></span>
    <span class="name">Kelvaro.ch</span>
  </div>
  <div class="services">
    <h2 class="services__title">our service listings</h2>
    <p class="services__list">Vehicle labeling<span class="dot"></span>Shop window labeling<br>Stickers and much more</p>
  </div>
</section>

<section class="card card--contact">
  <div class="brand">
    <span class="mark"></span>
    <span class="name">Kelvaro.ch</span>
  </div>
  <div class="divider"></div>
  <div class="details">
    <p class="person__name">Maren Holzer</p>
    <p class="person__role">Manager</p>
    <div class="row address">
      <svg viewBox="0 0 24 24"><path d="M12 2a7 7 0 0 0-7 7c0 5 7 13 7 13s7-8 7-13a7 7 0 0 0-7-7zm0 9.5A2.5 2.5 0 1 1 12 6.5a2.5 2.5 0 0 1 0 5z"/></svg>
      <span>Lindenweg 14<br>9406 Tarnbach</span>
    </div>
    <div class="row">
      <svg viewBox="0 0 24 24"><path d="M6.6 10.8a15 15 0 0 0 6.6 6.6l2.2-2.2a1 1 0 0 1 1-.25 11.4 11.4 0 0 0 3.6.57 1 1 0 0 1 1 1V20a1 1 0 0 1-1 1A17 17 0 0 1 3 4a1 1 0 0 1 1-1h3.5a1 1 0 0 1 1 1 11.4 11.4 0 0 0 .57 3.6 1 1 0 0 1-.25 1z"/></svg>
      <span>+41 ( 0 ) 79 482 6037</span>
    </div>
    <div class="row">
      <svg viewBox="0 0 24 24"><path d="M2 5h20v14H2zm2 2v.5l8 5 8-5V7zm0 2.9V17h16V9.9l-8 5z"/></svg>
      <span>info@kelvaro-example.ch</span>
    </div>
    <div class="row">
      <svg viewBox="0 0 24 24"><path d="M12 2a10 10 0 1 0 0 20 10 10 0 0 0 0-20zm6.9 9h-3a15 15 0 0 0-1.3-5.6A8 8 0 0 1 18.9 11zM12 4c.9 1.2 1.8 3.6 1.9 7h-3.8c.1-3.4 1-5.8 1.9-7zM9.4 5.4A15 15 0 0 0 8.1 11h-3a8 8 0 0 1 4.3-5.6zM5.1 13h3a15 15 0 0 0 1.3 5.6A8 8 0 0 1 5.1 13zM12 20c-.9-1.2-1.8-3.6-1.9-7h3.8c-.1 3.4-1 5.8-1.9 7zm2.6-1.4a15 15 0 0 0 1.3-5.6h3a8 8 0 0 1-4.3 5.6z"/></svg>
      <span>www.Kelvaro-example.ch</span>
    </div>
  </div>
</section>

</body>
</html>
```